Healthy lifestyle Influencer business card

I need your creativity to have a business card that I can leave in all the restaurants, hotels and spas I visit to inform them that I am an influencer specializing in the wellness sector and that I will write a review about them. You can use my instagram photos Lunavita27 or on my website www.piattileggeriorto.it. I would like my business card to impress with its creativity! thank you very much!

Contact Information for Business Card

siteweb, instagram, phone number

Font styles to use
Decorative
Script

Colors
0094D4
00A9DD
6FCCEA
C7EBF8
E9F6FB
59FF00
82FF00
B8FF75
E3FFCB
F4FFEA
FFC000
F8CF3A
FAE287
FDF2CF
FEFAEE
F0912C
F2A743
F7CA91
FBE8D2
FDF5EE
EE7325
F08F49
F5BC92
FAE3D3
FDF4ED
EB3D1F
EC4F4E
F09395
F8D3D4
FCEDEE
E54698
E96AAD
F1A4CE
F9D9EA
FCEFF6

Requirements
Nice to have
• creativity

```html
<!DOCTYPE html>
<html lang="it">
<head>
<meta charset="utf-8">
<title>Lunavita Cucina – Business Card</title>
<link href="https://fonts.googleapis.com/css2?family=Open+Sans:wght@400;600;700&display=swap" rel="stylesheet">
<style>
  :root {
    --stage: #262626;
    --card-dark: #4b4b4b;
    --card-light: #ffffff;
    --ink: #3f3f3f;
    --ink-soft: #5a5a5a;
    --arc: #5c5c5c;
    --photo-top: #c9c7d6;
    --photo-mid: #6d7488;
    --photo-low: #8a7a6a;
    --white: #ffffff;
    --accent: #e54698;
  }
  * { box-sizing: border-box; margin: 0; padding: 0; }
  html, body {
    width: 1200px; height: 1015px; overflow: hidden;
    background: var(--stage);
    font-family: "Open Sans", sans-serif;
  }
  .canvas { position: relative; width: 1200px; height: 1015px; }
  .card {
    position: absolute; width: 620px; height: 354px;
    box-shadow: 0 14px 30px rgba(0,0,0,.45);
    overflow: hidden;
  }
  .card--back { left: 90px; top: 100px; background: var(--card-dark); }
  .card--front { left: 490px; top: 560px; background: var(--card-light); }

  .brand-name {
    font-weight: 600; letter-spacing: .5px; white-space: nowrap;
  }
  .card--back .brand-name {
    position: absolute; left: 0; right: 0; top: 150px;
    text-align: center; font-size: 42px; color: var(--white);
  }
  .card-photo { position: absolute; inset: 0; }
  .card--front .brand-name {
    position: absolute; left: 70px; top: 150px;
    font-size: 28px; color: var(--ink-soft);
  }
  .social {
    position: absolute; right: 30px; top: 222px;
    display: flex; align-items: center; gap: 6px;
    font-size: 15px; color: var(--ink);
  }
  .social-mark { width: 14px; height: 14px; border-radius: 3px; background: var(--accent); }
  .contact { position: absolute; left: 70px; top: 228px; color: var(--ink); }
  .contact-name { font-size: 22px; font-weight: 700; line-height: 1.1; }
  .contact-role { font-size: 15px; margin-bottom: 14px; }
  .contact-line { display: flex; align-items: center; gap: 8px; font-size: 15px; line-height: 1.55; }
  .contact-line svg { width: 15px; height: 15px; flex: none; }
</style>
</head>
<body>
<main class="canvas">
  <section class="card card--back">
    <p class="brand-name">Lunavita Cucina</p>
  </section>

  <section class="card card--front">
    <svg class="card-photo" viewBox="0 0 620 354" width="620" height="354">
      <defs>
        <linearGradient id="tartTones" x1="0" y1="0" x2="0.3" y2="1">
          <stop offset="0" stop-color="var(--photo-top)"/>
          <stop offset="0.45" stop-color="var(--photo-mid)"/>
          <stop offset="0.8" stop-color="var(--photo-low)"/>
          <stop offset="1" stop-color="#eeeeee"/>
        </linearGradient>
      </defs>
      <path role="img" aria-label="Photo of a blueberry cheesecake tart on a white plate"
            d="M250,0 Q290,215 450,212 Q560,208 620,150 L620,0 Z" fill="url(#tartTones)"/>
      <path d="M250,0 Q290,215 450,212 Q560,208 620,150" fill="none" stroke="var(--arc)" stroke-width="5"/>
    </svg>

    <p class="brand-name">Lunavita Cucina</p>

    <div class="social">
      <span>@Lunavita27</span>
      <span class="social-mark"></span>
    </div>

    <div class="contact">
      <p class="contact-name">Marta Reali</p>
      <p class="contact-role">Managing Director</p>
      <p class="contact-line">
        <svg viewBox="0 0 24 24"><path d="M6.6 10.8a15 15 0 0 0 6.6 6.6l2.2-2.2a1 1 0 0 1 1-.25 11.4 11.4 0 0 0 3.6.57 1 1 0 0 1 1 1V20a1 1 0 0 1-1 1A17 17 0 0 1 3 4a1 1 0 0 1 1-1h3.5a1 1 0 0 1 1 1c0 1.25.2 2.45.57 3.57a1 1 0 0 1-.25 1z" fill="var(--ink)"/></svg>
        044-987 654 321
      </p>
      <p class="contact-line">
        <svg viewBox="0 0 24 24" fill="none" stroke="var(--ink)" stroke-width="2"><circle cx="12" cy="12" r="9"/><path d="M3 12h18M12 3c3 3 3 15 0 18M12 3c-3 3-3 15 0 18"/></svg>
        www.piattileggeriorto.it
      </p>
    </div>
  </section>
</main>
</body>
</html>
```